New Bicycle shop business card

Hi!
I'm looking for a business card for my new proffesional bike mechanics shop. This shop is only for fixing broken bikes and not selling bikes.
Peferbly a modern and sleek and modern design.
Colors: black, grey, red, white
Information:
Name: Rijwielwerkplaats Vanhoutte
Shop owner: Bart Vanhoutte & Marieke Segers
Website: www.rijwielwerkplaats-vanhoutte.be
Email: info@rijwielwerkplaats-vanhoutte.be
Phone number: +32471902368
Street adres: Kerkweg 46
9940 Bellebeke
Slogan/shop information: Herstellingen van alle merken.
Logo: see files.
Target Market(s)
People who seek a mechanic to fix or upgrade their bikes.
Contact Information for Business Card
Information:
Website: info@rijwielwerkplaats-vanhoutte.be
9940 Bellebeke
Logo: see files.

```html
<!DOCTYPE html>
<html lang="nl">
<head>
<meta charset="utf-8">
<title>Rijwielwerkplaats Vanhoutte – visitekaartje</title>
<link rel="stylesheet" href="https://fonts.googleapis.com/css2?family=Montserrat:wght@800&family=Roboto:wght@400;500&display=swap">
<style>
  :root {
    --red: #d42b3c;
    --black: #1c1a1b;
    --grey: #9a9c9f;
    --white: #ffffff;
    --backdrop: #e4e4e4;
  }
  * { margin: 0; padding: 0; box-sizing: border-box; }
  html, body { width: 1200px; height: 852px; overflow: hidden; }
  body {
    background: var(--backdrop);
    font-family: "Roboto", Arial, sans-serif;
    position: relative;
  }
  .card {
    position: absolute;
    top: 266px;
    width: 520px;
    height: 320px;
    border-radius: 22px;
    overflow: hidden;
  }
  .card--front { left: 50px; background: var(--red); }
  .card--back { left: 630px; background: var(--white); }

  .brand {
    display: flex;
    align-items: center;
    gap: 12px;
  }
  .brand__dot {
    width: 34px; height: 34px;
    border-radius: 50%;
    flex: none;
  }
  .brand__name {
    font-family: "Montserrat", Arial, sans-serif;
    font-weight: 800;
    font-size: 22px;
    line-height: 1.15;
    letter-spacing: 1px;
    text-transform: uppercase;
  }
  .card--front .brand {
    position: absolute; left: 0; right: 0; top: 112px;
    justify-content: center;
  }
  .card--front .brand__dot { background: var(--white); }
  .card--front .brand__name { color: var(--black); }

  .slogan {
    position: absolute; left: 0; right: 0; bottom: 44px;
    display: flex; align-items: center; justify-content: center; gap: 12px;
    color: var(--white);
    font-size: 13px;
  }
  .slogan::before, .slogan::after {
    content: ""; width: 34px; height: 2px; background: var(--white);
  }

  .card--back .brand {
    position: absolute; left: 26px; top: 92px;
  }
  .card--back .brand__dot { background: var(--red); }
  .card--back .brand__name { color: var(--black); font-size: 20px; }

  .wave { position: absolute; inset: 0; }

  .person {
    position: absolute; right: 30px; top: 22px; text-align: right;
  }
  .person__name {
    font-family: "Montserrat", Arial, sans-serif;
    font-weight: 800;
    font-size: 18px;
    letter-spacing: 1px;
    color: var(--red);
    text-transform: uppercase;
  }
  .person__role { font-size: 11px; color: var(--black); margin-top: 2px; }

  .contact {
    position: absolute; right: 26px; top: 200px;
    list-style: none;
    color: var(--white);
    font-size: 12px;
    text-align: right;
  }
  .contact li {
    display: flex; align-items: center; justify-content: flex-end; gap: 7px;
    height: 24px;
  }
  .contact svg { width: 13px; height: 13px; flex: none; }
  .contact .spacer { width: 13px; flex: none; }
</style>
</head>
<body>

<section class="card card--front" aria-label="Voorkant visitekaartje">
  <div class="brand">
    <span class="brand__dot"></span>
    <span class="brand__name">Rijwielwerkplaats<br>Vanhoutte</span>
  </div>
  <p class="slogan">Herstellingen van alle merken</p>
</section>

<section class="card card--back" aria-label="Achterkant visitekaartje">
  <svg class="wave" viewBox="0 0 520 320" aria-hidden="true">
    <path d="M0,320 L0,280 C120,278 200,230 270,190 C340,150 420,118 520,112 L520,320 Z" fill="var(--red)"/>
    <path d="M0,268 C120,266 200,218 270,178 C340,138 420,106 520,100" fill="none" stroke="var(--black)" stroke-width="5"/>
    <path d="M24,300 C120,298 180,270 228,242" fill="none" stroke="var(--grey)" stroke-width="6" stroke-linecap="round"/>
  </svg>

  <div class="person">
    <p class="person__name">Marieke Segers</p>
    <p class="person__role">Owner</p>
  </div>

  <div class="brand">
    <span class="brand__dot"></span>
    <span class="brand__name">Rijwielwerkplaats<br>Vanhoutte</span>
  </div>

  <ul class="contact">
    <li>+32471902368
      <svg viewBox="0 0 16 16"><path d="M3 1h3l1.5 4-2 1.3a9 9 0 0 0 4.2 4.2L11 8.5l4 1.5v3a2 2 0 0 1-2 2A12 12 0 0 1 1 3a2 2 0 0 1 2-2z" fill="var(--white)"/></svg>
    </li>
    <li>rijwielwerkplaats-vanhoutte.be
      <svg viewBox="0 0 16 16"><rect x="1" y="3" width="14" height="10" rx="1" fill="var(--white)"/><path d="M1.5 3.5 8 9l6.5-5.5" fill="none" stroke="var(--red)" stroke-width="1.3"/></svg>
    </li>
    <li>info@rijwielwerkplaats-vanhoutte.be
      <svg viewBox="0 0 16 16"><circle cx="8" cy="8" r="6.5" fill="none" stroke="var(--white)" stroke-width="1.4"/><ellipse cx="8" cy="8" rx="2.8" ry="6.5" fill="none" stroke="var(--white)" stroke-width="1.2"/><path d="M1.5 8h13" stroke="var(--white)" stroke-width="1.2"/></svg>
    </li>
    <li>Kerkweg 46 9940 Bellebeke<span class="spacer"></span></li>
  </ul>
</section>

</body>
</html>
```